Kelvinridge Climate Business Card Design

Design new, 2 sides, business cards for a residential and light commercial heating, air conditioning contractor.

Target Market(s)

Homeowners, small businesses

Industry/Entity Type

Business

Contact Information for Business Card

Dominic Westerhall
Phone - 862-415-2736
Email
Address - PO box 518
Brightwater NJ 07912
Website - www.HarborBreezeLLC.example

Requirements
Must have
• logo, company colors, standard size with no die cut, so I can use nova stamp

```html
<!DOCTYPE html>
<html lang="en">
<head>
<meta charset="utf-8">
<title>Kelvinridge Climate Business Card</title>
<link rel="stylesheet" href="https://fonts.googleapis.com/css2?family=Source+Sans+3:ital,wght@0,400;0,600;0,700;1,400&display=swap">
<style>
  :root {
    --page-bg: #dcd9d6;
    --card-light: #eceae8;
    --card-light-2: #dedad7;
    --accent-orange: #d9722a;
    --maroon-top: #7d1c2c;
    --maroon-bottom: #5c0f1e;
    --name-maroon: #7a1a2b;
    --contact-text: #f1dede;
    --tagline-text: #ecc9c9;
    --brand-gold: #e58a34;
  }
  * { margin: 0; padding: 0; box-sizing: border-box; }
  html, body {
    width: 1200px; height: 969px; overflow: hidden;
    background: var(--page-bg);
    font-family: "Source Sans 3", sans-serif;
  }
  .business-card {
    position: absolute; left: 75px; top: 185px;
    width: 1050px; height: 600px;
    background: linear-gradient(180deg, var(--card-light), var(--card-light-2));
    box-shadow: 0 10px 30px rgba(0,0,0,0.18);
    overflow: hidden;
  }
  .top-stripe {
    position: absolute; left: 0; top: 0; width: 100%; height: 14px;
    background: var(--accent-orange);
  }
  .lower-panel {
    position: absolute; left: 0; top: 241px; width: 100%; bottom: 0;
    background: linear-gradient(180deg, var(--maroon-top), var(--maroon-bottom));
  }
  .owner-name {
    position: absolute; left: 60px; top: 82px;
    font-size: 35px; font-weight: 600; letter-spacing: 0.5px;
    color: var(--name-maroon); text-transform: uppercase;
  }
  .owner-title {
    position: absolute; left: 60px; top: 128px;
    font-size: 27px; color: var(--accent-orange);
  }
  .brand-name {
    position: absolute; left: 556px; top: 196px; width: 442px;
    text-align: center;
    font-size: 54px; font-weight: 700; line-height: 58px;
    color: var(--brand-gold);
  }
  .address {
    position: absolute; left: 60px; top: 263px;
    font-size: 27px; line-height: 40px; color: var(--contact-text);
  }
  .contact-list {
    position: absolute; left: 60px; top: 366px;
    list-style: none; font-size: 27px; color: var(--contact-text);
  }
  .contact-list li {
    display: flex; align-items: center; height: 39.5px;
  }
  .contact-list svg {
    width: 26px; height: 26px; margin-right: 16px; flex: none;
    fill: var(--contact-text);
  }
  .tagline {
    position: absolute; right: 34px; top: 452px;
    text-align: right; font-style: italic;
    font-size: 26px; line-height: 37px; color: var(--tagline-text);
  }
</style>
</head>
<body>
  <div class="business-card">
    <div class="top-stripe"></div>
    <div class="lower-panel"></div>

    <div class="owner-name">Dominic Westerhall</div>
    <div class="owner-title">CEO/Founder</div>

    <div class="brand-name">Kelvinridge<br>Climate</div>

    <div class="address">PO Box 518<br>Brightwater, NJ 07912</div>

    <ul class="contact-list">
      <li>
        <svg viewBox="0 0 24 24" aria-hidden="true"><path d="M6.6 10.8c1.4 2.8 3.8 5.1 6.6 6.6l2.2-2.2c.3-.3.7-.4 1-.2 1.1.4 2.3.6 3.6.6.6 0 1 .4 1 1V20c0 .6-.4 1-1 1C10.6 21 3 13.4 3 4c0-.6.4-1 1-1h3.5c.6 0 1 .4 1 1 0 1.3.2 2.5.6 3.6.1.3 0 .7-.2 1l-2.3 2.2z"/></svg>
        862 415 2736
      </li>
      <li>
        <svg viewBox="0 0 24 24" aria-hidden="true"><path d="M7 1h10c1.1 0 2 .9 2 2v18c0 1.1-.9 2-2 2H7c-1.1 0-2-.9-2-2V3c0-1.1.9-2 2-2zm0 3v14h10V4H7zm5 15.2a1.2 1.2 0 100 2.4 1.2 1.2 0 000-2.4z"/></svg>
        862 415 2790
      </li>
      <li>
        <svg viewBox="0 0 24 24" aria-hidden="true"><path d="M7 2h10v5H7zM4 8h16c1.1 0 2 .9 2 2v7h-4v5H6v-5H2v-7c0-1.1.9-2 2-2zm4 8v4h8v-4H8zm10-5a1 1 0 100 2 1 1 0 000-2z"/></svg>
        862 415 2755
      </li>
      <li>
        <svg viewBox="0 0 24 24" aria-hidden="true"><path d="M2 5h20v14H2V5zm2 2v.5l8 5 8-5V7H4zm0 2.8V17h16V9.8l-8 5-8-5z"/></svg>
        dominic@kelvinridgellc.example
      </li>
      <li>
        <svg viewBox="0 0 24 24" aria-hidden="true"><path d="M12 2a10 10 0 100 20 10 10 0 000-20zm6.9 6h-3a15 15 0 00-1.3-3.9A8 8 0 0118.9 8zM12 4c.9 1.2 1.6 2.5 2 4h-4c.4-1.5 1.1-2.8 2-4zM4.3 14a8 8 0 010-4h3.4a16 16 0 000 4H4.3zm.8 2h3a15 15 0 001.3 3.9A8 8 0 015.1 16zm3-8h-3a8 8 0 014.3-3.9C8.8 5.3 8.4 6.6 8.1 8zM12 20c-.9-1.2-1.6-2.5-2-4h4c-.4 1.5-1.1 2.8-2 4zm2.3-6H9.7a14 14 0 010-4h4.6a14 14 0 010 4zm.3 5.9c.6-1.2 1-2.5 1.3-3.9h3a8 8 0 01-4.3 3.9zm1.7-5.9a16 16 0 000-4h3.4a8 8 0 010 4h-3.4z"/></svg>
        www.KelvinridgeLLC.example
      </li>
    </ul>

    <div class="tagline">Residential &amp;<br>light commercial heating<br>Air conditioning contractor</div>
  </div>
</body>
</html>
```